Harborline Auto LLC

Car Dealer Customer Service
Address: 2874 Cresthaven Road, Shelbyville, TN 37162
web: www.harborlineautoxq.net
email: harborlineautoxq@mailnest.example
Phone: (931) 555-0148
Phone: (629) 555-0173

```html
<!DOCTYPE html>
<html lang="en">
<head>
<meta charset="utf-8">
<title>Harborline Auto – Business Card</title>
<link rel="stylesheet" href="https://fonts.googleapis.com/css2?family=Montserrat:wght@700;800&family=Roboto:wght@400;500&display=swap">
<style>
  :root {
    --stage: #3a3a3a;
    --card-white: #ffffff;
    --card-black: #161616;
    --brand-blue: #1e6fa8;
    --bright-blue: #2a8fd0;
    --brand-gold: #f0b032;
    --text-gray: #5a5a5a;
    --pattern-dark: #0e0e0e;
    --pattern-light: #2a2a2a;
  }
  * { margin: 0; padding: 0; box-sizing: border-box; }
  html, body { width: 1200px; height: 801px; overflow: hidden; }
  body {
    background: var(--stage);
    display: flex;
    align-items: center;
    justify-content: center;
    gap: 40px;
    font-family: "Roboto", Arial, sans-serif;
  }
  .card {
    position: relative;
    width: 540px;
    height: 309px;
    border-bottom: 3px solid var(--bright-blue);
    overflow: hidden;
  }
  /* Front */
  .card-front { background: var(--card-white); display: flex; align-items: center; }
  .brand-block {
    width: 270px;
    display: flex;
    align-items: center;
    justify-content: center;
    gap: 12px;
  }
  .brand-dot {
    width: 44px; height: 44px; border-radius: 50%;
    background: var(--bright-blue);
    flex: none;
  }
  .brand-name {
    font-family: "Montserrat", Arial, sans-serif;
    font-weight: 800;
    font-size: 24px;
    line-height: 1.05;
    color: var(--brand-blue);
    text-transform: uppercase;
  }
  .divider {
    width: 1.5px; height: 110px;
    background: var(--brand-blue);
    margin-right: 18px;
    flex: none;
  }
  .contact-block { flex: 1; }
  .contact-title {
    font-family: "Roboto", Arial, sans-serif;
    font-weight: 500;
    font-size: 15px;
    color: var(--brand-blue);
    margin-bottom: 4px;
  }
  .contact-address { font-size: 13px; color: var(--text-gray); line-height: 1.35; margin-bottom: 6px; }
  .contact-list { list-style: none; }
  .contact-list li {
    display: flex; align-items: center; gap: 6px;
    font-size: 12px; color: var(--text-gray); line-height: 1.55;
    white-space: nowrap;
  }
  .contact-list svg { width: 10px; height: 10px; flex: none; fill: var(--brand-gold); }
  /* Back */
  .card-back { background: var(--card-black); }
  .back-pattern {
    position: absolute; inset: 0;
    background: linear-gradient(135deg, var(--pattern-dark) 0%, var(--pattern-light) 100%);
  }
  .back-brand {
    position: absolute; left: 50%; top: 50%;
    transform: translate(-50%, -50%);
    display: flex; align-items: center; gap: 10px;
  }
  .back-brand .brand-dot { width: 36px; height: 36px; }
  .back-brand .brand-name { color: var(--brand-gold); font-size: 20px; }
</style>
</head>
<body>
  <section class="card card-front">
    <div class="brand-block">
      <span class="brand-dot"></span>
      <span class="brand-name">Harborline<br>Auto</span>
    </div>
    <div class="divider"></div>
    <div class="contact-block">
      <h2 class="contact-title">Car Dealer Customer Service</h2>
      <p class="contact-address">2874 Cresthaven Road<br>Shelbyville, TN 37162</p>
      <ul class="contact-list">
        <li><svg viewBox="0 0 10 10"><path d="M2 0.5 3.6 2.6 2.7 3.7C3.3 5 4.9 6.7 6.3 7.3L7.4 6.4 9.5 8 8.3 9.5C4.5 9.3 0.7 5.5 0.5 1.7Z"/></svg>(931) 555-0148</li>
        <li><svg viewBox="0 0 10 10"><path d="M2.5 0h5a1 1 0 0 1 1 1v8a1 1 0 0 1-1 1h-5a1 1 0 0 1-1-1V1a1 1 0 0 1 1-1Zm0.5 1.3v6.2h4V1.3Z"/></svg>(629) 555-0173</li>
        <li><svg viewBox="0 0 10 10"><path d="M0 2h10v6H0Zm1 1 4 3 4-3Z"/></svg>harborlineautoxq@mailnest.example</li>
        <li><svg viewBox="0 0 10 10"><path d="M5 0a5 5 0 1 0 0 10A5 5 0 0 0 5 0Zm0 1c.8 0 1.6 1.6 1.7 3.5H3.3C3.4 2.6 4.2 1 5 1Zm-1.7 4.5h3.4C6.6 7.4 5.8 9 5 9s-1.6-1.6-1.7-3.5Z"/></svg>www.harborlineautoxq.net</li>
      </ul>
    </div>
  </section>

  <section class="card card-back">
    <div class="back-pattern" role="img" aria-label="Embossed repeating pattern of gear and vintage car emblems on black"></div>
    <div class="back-brand">
      <span class="brand-dot"></span>
      <span class="brand-name">Harborline Auto</span>
    </div>
  </section>
</body>
</html>
```